8 x 8 Social Media Design - Tax, Accounting & Bookkeeping Service

Bright Path Ledger Group, Inc.

Tax, Accounting and Bookkeeping Services

“We provide our services, with you next mortgage in mind”

Special pricing available for all Mortgage Loan Customers!!

President / CEO Marcus Delaney

Primary service provider with over 27 years of experience

Call directly for more information: (240) 555-0193

Or email at: mdelaney@brightpathledger.com

```html
<!DOCTYPE html>
<html lang="en">
<head>
<meta charset="UTF-8">
<title>Bright Path Ledger Group – Tax, Accounting and Bookkeeping Services</title>
<link rel="stylesheet" href="https://fonts.googleapis.com/css2?family=Poppins:wght@500;600;700;800&family=Great+Vibes&display=swap">
<style>
  :root {
    --stage: #b3b3b3;
    --navy-deep: #071538;
    --navy: #0b2170;
    --royal: #1437b8;
    --gold: #e3b24a;
    --gold-light: #f6dc9a;
    --gold-dark: #b9821f;
    --ink: #0a1433;
    --white: #ffffff;
  }
  * { margin: 0; padding: 0; box-sizing: border-box; }
  html, body { width: 1200px; height: 562px; overflow: hidden; background: var(--stage); }
  body { position: relative; font-family: "Poppins", sans-serif; }

  .post {
    position: absolute; left: 330px; top: 11px;
    width: 540px; height: 540px; overflow: hidden;
    background: var(--navy-deep);
    box-shadow: 0 8px 24px rgba(0,0,0,.25);
  }
  .gold-edge {
    position: absolute; left: 0; top: 0; width: 25px; height: 540px;
    background: linear-gradient(90deg, var(--gold-light), #fff6df 45%, var(--gold) 100%);
  }
  .main-panel {
    position: absolute; left: 25px; top: 0; width: 338px; height: 540px;
    background: linear-gradient(180deg, var(--navy-deep) 0%, var(--navy-deep) 45%, var(--navy) 62%, var(--royal) 85%, var(--navy) 100%);
  }
  .stripes {
    position: absolute; left: 25px; top: 0; width: 338px; height: 120px;
    background: repeating-linear-gradient(90deg, rgba(30,70,200,.55) 0 14px, transparent 14px 32px);
    -webkit-mask-image: linear-gradient(180deg, #000 20%, transparent 100%);
            mask-image: linear-gradient(180deg, #000 20%, transparent 100%);
  }
  .corner-glow {
    position: absolute; left: -40px; bottom: -50px; width: 130px; height: 130px; border-radius: 50%;
    background: radial-gradient(circle, var(--gold-light) 0%, rgba(227,178,74,.6) 45%, transparent 72%);
  }

  .photo { position: absolute; }
  .photo--couple {
    left: 366px; top: 0; width: 174px; height: 190px;
    background: linear-gradient(135deg, #c9b79a, #7d8fb6 55%, #d9d35a);
    border-left: 3px solid var(--gold); border-bottom: 3px solid var(--gold);
  }
  .photo--family {
    left: 366px; top: 193px; width: 174px; height: 347px;
    background: linear-gradient(160deg, #ece3d4, #b99a6e 60%, #8a6a43);
    border-left: 3px solid var(--gold);
  }
  .photo--ceo {
    left: 300px; top: 290px; width: 240px; height: 250px;
    background: radial-gradient(ellipse at 55% 30%, #3a2c25 0%, #15151c 55%, #0c0c12 100%);
    border-radius: 110px 110px 0 0;
  }

  .brand {
    position: absolute; left: 25px; top: 48px; width: 338px;
    display: flex; align-items: center; justify-content: center; gap: 8px;
  }
  .brand-dot { width: 14px; height: 14px; border-radius: 50%; background: var(--gold); }
  .brand-name {
    font-weight: 700; font-size: 17px; color: var(--gold); letter-spacing: .3px;
    text-align: center; line-height: 1.15;
  }

  .headline {
    position: absolute; left: 25px; top: 132px; width: 338px;
    text-align: center; color: var(--white);
    font-weight: 800; font-size: 29px; line-height: 32px;
    text-shadow: 0 0 12px rgba(246,220,154,.55);
  }
  .subline {
    position: absolute; left: 25px; top: 246px; width: 338px;
    text-align: center; color: var(--gold);
    font-weight: 600; font-size: 15.5px; line-height: 19px;
  }

  .ribbon {
    position: absolute; left: 14px; top: 310px; width: 345px; height: 69px;
    background: linear-gradient(90deg, var(--gold-dark), var(--gold) 25%, var(--gold-light) 55%, var(--gold) 85%, var(--gold-dark));
    color: var(--ink); text-align: center; padding-top: 10px;
  }
  .ribbon-top { font-weight: 600; font-size: 15px; line-height: 26px; }
  .ribbon-top strong { font-weight: 700; font-size: 24px; letter-spacing: .5px; }
  .ribbon-bottom { font-weight: 600; font-size: 14px; line-height: 18px; }

  .experience-box {
    position: absolute; left: 76px; top: 404px; width: 150px; height: 47px;
    background: var(--royal); border-radius: 8px;
    padding: 6px 0 0 9px; line-height: 17px;
  }
  .experience-box .line1 { color: var(--white); font-weight: 500; font-size: 15px; }
  .experience-box .line2 { color: var(--gold); font-weight: 500; font-size: 14px; }

  .years-badge {
    position: absolute; left: 228px; top: 398px; width: 80px; height: 62px; text-align: center;
  }
  .years-badge .num { color: var(--white); font-weight: 800; font-size: 30px; line-height: 28px; }
  .years-badge .unit { color: var(--white); font-weight: 700; font-size: 9px; line-height: 11px; }
  .years-badge .label {
    display: inline-block; margin-top: 3px; padding: 1px 7px;
    background: var(--gold); color: var(--white); border-radius: 3px;
    font-weight: 700; font-size: 7.5px; letter-spacing: .3px;
  }

  .contact { position: absolute; left: 95px; top: 472px; }
  .contact-row { display: flex; align-items: center; gap: 8px; color: var(--white); }
  .contact-row--phone { font-weight: 600; font-size: 22px; line-height: 26px; }
  .contact-row--email { font-weight: 600; font-size: 11.5px; margin-top: 3px; }
  .contact-row svg { flex: none; }

  .signature {
    position: absolute; left: 325px; top: 455px; width: 200px; text-align: center;
  }
  .signature-name {
    font-family: "Great Vibes", cursive; color: var(--white); font-size: 28px; line-height: 34px;
  }
  .signature-title {
    display: inline-block; margin-top: 3px; padding: 1px 12px;
    background: var(--gold); color: var(--ink); border-radius: 12px;
    font-weight: 600; font-size: 11px; line-height: 18px;
  }
</style>
</head>
<body>
  <main class="post">
    <div class="gold-edge"></div>
    <div class="main-panel"></div>
    <div class="stripes"></div>

    <div class="photo photo--couple" role="img" aria-label="Photo of a couple reviewing paperwork together at a table"></div>
    <div class="photo photo--family" role="img" aria-label="Photo of a happy family relaxing among moving boxes in a new home"></div>
    <div class="photo photo--ceo" role="img" aria-label="Portrait of the company president in a dark hat, glasses and dark coat"></div>

    <div class="corner-glow"></div>

    <div class="brand">
      <span class="brand-dot"></span>
      <span class="brand-name">Bright Path Ledger<br>Group, Inc.</span>
    </div>

    <h1 class="headline">Tax, Accounting<br>and Bookkeeping<br>Services</h1>
    <p class="subline">We provide our services, with<br>you next mortgage in mind</p>

    <div class="ribbon">
      <div class="ribbon-top">Special pricing <strong>AVAILABLE</strong></div>
      <div class="ribbon-bottom">for all Mortgage Loan Customers!!</div>
    </div>

    <div class="experience-box">
      <div class="line1">Primary service</div>
      <div class="line2">provider with over</div>
    </div>
    <div class="years-badge">
      <div class="num">27</div>
      <div class="unit">YEARS</div>
      <div class="label">EXPERIENCE</div>
    </div>

    <div class="contact">
      <div class="contact-row contact-row--phone">
        <svg width="20" height="20" viewBox="0 0 24 24" aria-hidden="true"><path fill="#e3b24a" d="M6.6 10.8a15.1 15.1 0 0 0 6.6 6.6l2.2-2.2c.3-.3.7-.4 1-.2 1.1.4 2.3.6 3.6.6.6 0 1 .4 1 1V20c0 .6-.4 1-1 1A17 17 0 0 1 3 4c0-.6.4-1 1-1h3.5c.6 0 1 .4 1 1 0 1.3.2 2.5.6 3.6.1.3 0 .7-.2 1z"/></svg>
        (240) 555-0193
      </div>
      <div class="contact-row contact-row--email">
        <svg width="18" height="12" viewBox="0 0 18 12" aria-hidden="true"><rect x=".5" y=".5" width="17" height="11" rx="1" fill="#ffffff"/><path d="M1 1l8 6 8-6" fill="none" stroke="#0b2170" stroke-width="1.4"/></svg>
        mdelaney@brightpathledger.com
      </div>
    </div>

    <div class="signature">
      <div class="signature-name">Marcus Delaney</div>
      <div class="signature-title">President / CEO</div>
    </div>
  </main>
</body>
</html>
```